New business card/stationary for a consulting company

I am looking for a clean and very professional looking business card for my consulting company as well as corresponding stationary. I am uploading our logo. I like simple and powerful for the feel. No graphics but I am open on everything else. Below is my contact information but would like the final to be in a version I can add my employees information into and print. Thank you.

Daniel Whitcombe
dan@ferncliffadvisory.com
2870 North 9th Avenue, Summit Floor, Elm Ridge, Illinois 60531
www.ferncliffadvisory.com

Industry/Entity Type

Consulting

Contact Information for Business Card

Daniel Whitcombe
dan@ferncliffadvisory.com
www.ferncliffadvisory.com

Font styles to use
Serif
Sans Serif

Requirements
Must have
• Our logo and the business card details.
Nice to have
• our website www.ferncliffadvisory.com

```html
<!DOCTYPE html>
<html lang="en">
<head>
<meta charset="utf-8">
<title>Ferncliff Advisory — Business Card</title>
<link href="https://fonts.googleapis.com/css2?family=Roboto:wght@400;500&display=swap" rel="stylesheet">
<style>
  :root {
    --backdrop: #3b3b3d;
    --card: #1e1e20;
    --accent: #1d9ee0;
    --ink-light: #f2f2f2;
    --mark-muted: #4d4d52;
  }
  * { margin: 0; padding: 0; box-sizing: border-box; }
  html, body { width: 799px; height: 1200px; overflow: hidden; }
  body {
    background: var(--backdrop);
    font-family: "Roboto", Arial, sans-serif;
    position: relative;
  }
  .card {
    position: absolute;
    left: 80px;
    width: 640px;
    height: 366px;
    background: var(--card);
    border-radius: 4px;
    box-shadow: 0 12px 30px rgba(0,0,0,0.45);
  }
  .card--front { top: 100px; }
  .card--back { top: 700px; }

  .front-mark {
    position: absolute;
    inset: 0;
    display: flex;
    align-items: center;
    justify-content: center;
    gap: 14px;
  }
  .front-mark__square {
    width: 26px; height: 26px;
    background: var(--mark-muted);
  }
  .front-mark__name {
    font-size: 34px;
    font-weight: 500;
    letter-spacing: 4px;
    color: var(--mark-muted);
  }

  .holder-name {
    position: absolute;
    left: 40px; top: 40px;
    font-size: 24px;
    font-weight: 400;
    letter-spacing: 2px;
    color: var(--accent);
    text-transform: uppercase;
  }
  .contact {
    position: absolute;
    left: 40px; top: 178px;
    list-style: none;
    color: var(--ink-light);
    font-size: 15px;
    line-height: 22px;
  }
  .contact__item { display: flex; align-items: center; gap: 10px; }
  .contact__icon { width: 13px; height: 13px; flex: none; }
  .contact__address { margin-top: 2px; }

  .back-mark {
    position: absolute;
    right: 40px; bottom: 40px;
    display: flex;
    align-items: center;
    gap: 10px;
  }
  .back-mark__square {
    width: 22px; height: 22px;
    background: var(--accent);
  }
  .back-mark__name {
    font-size: 20px;
    font-weight: 500;
    letter-spacing: 2px;
    color: var(--accent);
  }
</style>
</head>
<body>
  <section class="card card--front">
    <div class="front-mark">
      <span class="front-mark__square"></span>
      <span class="front-mark__name">FERNCLIFF ADVISORY</span>
    </div>
  </section>

  <section class="card card--back">
    <h1 class="holder-name">Daniel Whitcombe</h1>
    <ul class="contact">
      <li class="contact__item">
        <svg class="contact__icon" viewBox="0 0 14 14"><rect x="0.5" y="2.5" width="13" height="9" fill="var(--accent)"/><path d="M0.5 2.5 L7 8 L13.5 2.5" fill="none" stroke="#1e1e20" stroke-width="1.2"/></svg>
        <span>dan@ferncliffadvisory.com</span>
      </li>
      <li class="contact__item">
        <svg class="contact__icon" viewBox="0 0 14 14"><circle cx="7" cy="7" r="6.5" fill="var(--accent)"/><path d="M1 7 H13 M7 1 C4 4 4 10 7 13 M7 1 C10 4 10 10 7 13" fill="none" stroke="#1e1e20" stroke-width="1"/></svg>
        <span>www.ferncliffadvisory.com</span>
      </li>
      <li class="contact__address">2870 North 9th Avenue, Summit<br>Floor, Elm Ridge, Illinois 60531</li>
    </ul>
    <div class="back-mark">
      <span class="back-mark__square"></span>
      <span class="back-mark__name">FERNCLIFF ADVISORY</span>
    </div>
  </section>
</body>
</html>
```